Field Basket - Store need a label design

We need a Label Design for our Cosmetic Line with Hemp Cosmetics. We do not want a hemp leaf on our design. We want our LOGO infront of the design with the name of the product (shower gel, body lotion, .....) The ingredients must be included as well as in the bottle within 12 months. The font is smaller than 3mm. Generally, the font must be at least 2mm in size. What we need: 100x140mm 200ml E 12m 4x as: Hemp - shampoo, shower gel, body lotion and hair balm 20x66 mm 50g E (2 pieces for front and back) as: face cream, hand cream 42x52mm as: lip balm (sample how it should look in the uploaded files with the name morvil) What else should be on it: WITHOUT artificial colors and fragrances WITHOUT paraffins WITHOUT silicones with pure hemp seed oil Product not tested on animals Manufacturer: MORVIL A-4812 GRUNDLACH Description: HANF-SHAMPOO 200 ml Skin-mild washing-active ingredients develop a particularly pleasant and gentle cleansing effect. High-quality hemp seed oil nourishes the hair in a natural way and makes it pleasantly soft, loose and supple. BRISK MEADOW- is suitable for all hair types, especially for damaged and dull hair. HEMP SHOWER BATH 200 ml The pleasant foam cleans mildly and gently. The excellent care effect of natural hemp seed oil makes skin and hair pleasantly soft and supple.BRISK MEADOW- is suitable for mild cleansing and care, especially of sensitive skin and damaged hair. HEMP-FOAM BATH 200 ml Skin-mild washing-active ingredients develop a particularly mild and creamy foam. The excellent care effect of natural hemp seed oil makes the skin exceptionally soft and supple.BRISK MEADOW- is suitable for mild cleansing and care, especially of sensitive, rough and chapped skin. HEMP HAIR BALM 200 ml A special combination of natural hemp seed oil and other high-quality vegetable oils cares for the hair perfectly and makes it pleasantly soft, loose, supple, naturally shiny, extremely easy to style and effectively prevents the cleavage of the tips. BRISK MEADOW HEMP HAIR BALM is suitable for all hair types, especially for damaged, damaged, brittle and dull hair, as well as split hair tips. HEMP BODY LOTION 200 ml Pure Hemp Seed Oil nourishes the skin naturally, prevents it from drying out too much and makes it particularly soft and supple.BRISK MEADOW HEMP BODY LOTION is for pleasant body care, especially after bathing, especially in dry, brittle and sensitive skin HEMP FACE CREAM 50 g The particularly high content of pure hemp seed oil nourishes the skin perfectly and makes it unusually soft and supple.BRISK MEADOW HEMP FACE CREAM is suitable for pleasant and moisturizing care of the entire face, especially for dry and brittle skin Skin. HEMP HAND CREAM 50 g The high content of pure hemp seed oil and natural beeswax protects and nourishes the skin perfectly and makes it soft and supple. BRISK MEADOW HEMP HAND CREAM is suitable for protective care especially of stressed, sensitive and brittle skin. HEMP LIP BALM 6 g Natural hemp seed oil, pure beeswax and other valuable ingredients provide long-lasting care for the lips and protect them from adverse weather conditions and dehydration.BRISK MEADOW HEMP LIP BALM is particularly suitable for the lasting care of sensitive, brittle and torn lips. HANF-SHAMPOO Ingredients (INCI): Aqua, Sodium Laureth Sulfate, TEA-Lauryl Sulfate, Disodium Laureth Sulfosuccinate, Potassium Cocoyl Hydrolized Collagen, Linoleamide-DEA, Cannabis Sativa Seed Oil, Natural Perfume, Sodium Chloride, Citric Acid, Potassium Sorbate, Panthenol , Tocopherol, chlorophyll, citral *, citronellol *, geraniol *, limonene *, linalool *. (* natural ingredients of essential oils). HEMP-DUSCHBAD Ingredients (INCI): Aqua, Sodium Laureth Sulfate, TEA-Lauryl Sulfate, Disodium Laureth Sulfosuccinate, Potassium Cocoyl Hydrolized Collagen, Cocoamphodiacetate, Linoleamide-DEA, Cocamidopropylamine Oxide, Cannabis Sativa Seed Oil, Natural Perfume, Coco-Glucoside, Glyceryl Oleate, Sodium Chloride, Citric Acid, Potassium Sorbate, Panthenol, Tocopherol, Chlorophyll, Citral *, Citronellol *, Geraniol *, Limonene *, Linalool *. (* natural ingredients of essential oils). HANF-SCHAUMBAD Ingredients (INCI): Aqua, MIPA-Pareth-25-Sulfate, Cocamidopropyl Betaine, Disodium Laureth Sulfosuccinate, Linoleamide-DEA, Cannabis Sativa Seed Oil, Coco-Glucoside, Glyceryl Oleate, Natural Perfume, Panthenol, Potassium Sorbate, Citric Acid, tocopherol, chlorophyll, citral *, citronellol *, geraniol *, limonene *, linalool *. * (* Natural constituents of essential oils). HANF-HAARBALSAM Ingredients (INCI): Aqua, Ceteareth-20, Cetearyl Alcohol, Dicocodimonium Chloride, Glycerine, Cannabis Sativa Seed Oil, Coco-Glucoside, Glyceryl Oleate, Natural Perfume, Potassium Sorbate, Panthenol, Citric Acid, Tocopherol, Chlorophyll, Citral *, Citronellol *, geraniol *, limonene *, linalool *. (* natural ingredients of essential oils). Hemp Facial Ingredients (INCI): Aqua, Cannabis Sativa Seed Oil, Cetearyl Alcohol, Cetearyl Glucoside, Sodium Cetearyl Sulfate, Hexyl Decanol, Glycerine, Natural Perfume, Benzyl Alcohol, Potassium Sorbate, Sodium Benzoate, Tocopherol, Panthenol, Citric Acid, Citral * , Citronellol *, geraniol *, limonene *, linalool *. (* natural ingredients of essential oils). HANF HAND CREAM Ingredients (INCI): Cannabis sativa Seed Oil, Cocos Nucifera Oil, Cera Alba, Tocopherol, Natural Perfume, Citral *, Citronellol *, Geraniol *, Limonene *, Linalool *. (* natural ingredients of essential oils). HEMP BODY LOTION INGREDIENTS (INCI): Aqua, Cannabis Sativa Seed Oil, Cetearyl Alcohol, Ceteareth-12, Cetearyl Glucoside, Glycerol, Hexyldecanol, Natural Perfume, Benzyl Alcohol, Potassium Sorbate, Sodium Benzoate, Tocopherol, Panthenol, Citric Acid, Geraniol , Limonene *, linalool *, citronellol *, citral *, (* natural constituents of essential oils). HEMP LIP BALM Ingredients (INCI): Cannabis sativa Seed Oil, Cocos nucifera Oil, Cera Alba, Natural Perfume, Citral *, Citronellol *, Geraniol *, Limonene *, Linalool *. (* natural ingredients of essential oils).

Colors

Designer to choose colors to be used in the design.

Requirements
Must have
• The Sentence: Natural Spirit - Feel the nature should be in front of the label as our slogan for the Cosmetic Line
Should not have
• Hemp leaf

```html
<!DOCTYPE html>
<html lang="de">
<head>
<meta charset="utf-8">
<title>Hanf Kosmetik Etiketten</title>
<link rel="stylesheet" href="https://fonts.googleapis.com/css2?family=Oswald:wght@500;600&family=Nunito+Sans:wght@300;400;700;800&display=swap">
<style>
  :root{
    --green:#1f7a56; --green-2:#2f9a6c;
    --blue:#3c6db3; --blue-2:#5a8ad0;
    --brown:#6b4a2c; --brown-2:#8c6640;
    --gold:#c28428; --gold-2:#dca446;
    --wine:#7a3552; --wine-2:#9a5070;
    --lip:#4f7fbe; --lip-2:#7ca4d8;
    --grey:#7b7d94; --grey-2:#9a9cb0;
    --violet:#6a3d94; --violet-2:#8a62b2;
    --ink:#ffffff;
    --badge-dark:rgba(0,0,0,.38);
    --name-font:"Oswald",sans-serif;
    --text-font:"Nunito Sans",sans-serif;
  }
  *{box-sizing:border-box;margin:0;padding:0}
  html,body{width:846px;height:1200px;overflow:hidden;background:#fff}
  body{position:relative;font-family:var(--text-font);color:var(--ink)}

  .label{position:absolute;overflow:hidden}
  .label .texture{position:absolute;inset:0}
  .label > *:not(.texture){position:absolute}

  .tone-green .texture{background:linear-gradient(125deg,var(--green-2),var(--green) 45%,#155c40)}
  .tone-blue .texture{background:linear-gradient(125deg,var(--blue),var(--blue-2) 55%,#325f9e)}
  .tone-brown .texture{background:linear-gradient(125deg,var(--brown-2),var(--brown) 50%,#57391f)}
  .tone-gold .texture{background:linear-gradient(125deg,var(--gold-2),var(--gold) 50%,#a96f1e)}
  .tone-wine .texture{background:linear-gradient(125deg,var(--wine-2),var(--wine) 50%,#632841)}
  .tone-lip .texture{background:linear-gradient(125deg,var(--lip-2),var(--lip) 55%,#4070ad)}
  .tone-grey .texture{background:linear-gradient(125deg,var(--grey-2),var(--grey) 55%,#6a6c82)}
  .tone-violet .texture{background:linear-gradient(125deg,var(--violet-2),var(--violet) 55%,#583080)}

  .brand{display:flex;flex-direction:column;align-items:center;gap:3px;text-align:center}
  .brand .dot{width:28px;height:28px;border-radius:50%;background:var(--ink)}
  .brand .brand-name{font-family:var(--text-font);font-weight:700;font-size:10px;letter-spacing:.5px}

  .product-name{font-family:var(--name-font);font-weight:600;font-size:25px;letter-spacing:.3px;text-align:center;white-space:nowrap}
  .slogan{border-top:1.5px solid var(--ink);border-bottom:1.5px solid var(--ink);font-family:var(--name-font);font-weight:500;font-size:8px;letter-spacing:5px;text-align:center;padding:5px 0 4px}

  .claims{list-style:none;font-size:8px;font-weight:300}
  .claims li{border-bottom:1px solid rgba(255,255,255,.7);padding:2px 0 2px 2px;width:fit-content;min-width:60px}
  .claims li:last-child{border-bottom:none}

  .badge{background:var(--badge-dark);font-family:var(--name-font);font-weight:500;font-size:5.5px;letter-spacing:1px;line-height:1.9;padding:5px 7px}

  .copy{font-size:7.6px;font-weight:300;line-height:1.32}
  .copy strong{font-weight:800}
  .inci{font-size:4.9px;line-height:1.38;font-weight:400}

  .facts{display:flex;border-top:1px solid var(--ink);height:34px;align-items:center}
  .facts > div{flex:1;display:flex;align-items:center;justify-content:center;height:26px}
  .facts > div + div{border-left:1px solid var(--ink)}
  .facts .qty{font-size:17px;font-weight:400}
  .facts .qty small{font-size:9px}
  .facts .estim{font-size:19px;font-weight:300}
  .maker{font-size:4.6px;font-weight:700;letter-spacing:.1px}

  /* big labels 389 x 278 */
  .big{width:389px;height:278px}
  .big .brand{left:0;width:195px;top:11px}
  .big .product-name{left:0;width:195px;top:68px}
  .big .slogan{left:12px;width:171px;top:112px}
  .big .claims{left:10px;top:147px}
  .big .badge{left:8px;top:233px}
  .big .copy{left:228px;width:150px;top:14px}
  .big .inci{left:228px;width:150px}
  .big .facts{left:228px;width:150px;top:224px}
  .big .maker{left:234px;top:260px}
</style>
</head>
<body>

<!-- Duschbad -->
<section class="label big tone-green" style="left:23px;top:21px">
  <div class="texture" role="img" aria-label="Fließende grüne Textur als Hintergrund"></div>
  <div class="brand"><span class="dot"></span><span class="brand-name">BRISK MEADOW</span></div>
  <h2 class="product-name">HANF-DUSCHBAD</h2>
  <p class="slogan">FEEL THE NATURE</p>
  <ul class="claims"><li>OHNE künstliche Farb und Geruchstoffe</li><li>OHNE Paraffine</li><li>OHNE Silikone</li><li>Mit reinem Hanfsamenöl</li></ul>
  <p class="badge">PRODUKT NICHT<br>AN TIEREN GETESTET</p>
  <p class="copy">Der angenehme Schaum reinigt mild und schonend. Die hervorragende Pflegewirkung von naturreinem Hanfsamen-Öl macht Haut und Haar angenehm weich und geschmeidig.<br><br><strong>HANF-DUSCHBAD</strong> - eignet sich zur milden Reinigung und Pflege, besonders von empfindlicher Haut und strapaziertem Haar.</p>
  <p class="inci" style="top:131px">Ingredients (INCI): Aqua, Sodium Laureth Sulfate, TEA-Lauryl Sulfate, Disodium Laureth Sulfosuccinate, Potassium Cocoyl Hydrolized Collagen, Cocoamphodiacetate, Linoleamide-DEA, Cocamidopropylamine Oxide, Cannabis Sativa Seed Oil, Natural Perfume, Coco-Glucoside, Glyceryl Oleate, Sodium Chloride, Citric Acid, Potassium Sorbate, Panthenol, Tocopherol, Chlorophyll, Citral*, Citronellol*, Geraniol*, Limonene*, Linalool*<br>(* natürliche Bestandteile ätherischer Öle).</p>
  <div class="facts"><div class="qty">200<small>ml</small></div><div class="estim">e</div><div><svg width="22" height="20" viewBox="0 0 22 20" fill="none" stroke="#fff" stroke-width="1"><path d="M3 8h16l-1.5 10h-13z"/><path d="M4 8l12-6"/><text x="7" y="16" font-size="5" fill="#fff" stroke="none" font-family="sans-serif">12m</text></svg></div></div>
  <p class="maker">HERSTELLER: MORVIL NATURKOSMETIK A- 4812 GRUNDLACH</p>
</section>

<!-- Shampoo -->
<section class="label big tone-blue" style="left:436px;top:21px">
  <div class="texture" role="img" aria-label="Fließende blaue Textur als Hintergrund"></div>
  <div class="brand"><span class="dot"></span><span class="brand-name">BRISK MEADOW</span></div>
  <h2 class="product-name">HANF - SHAMPOO</h2>
  <p class="slogan">FEEL THE NATURE</p>
  <ul class="claims" style="top:158px"><li>OHNE künstliche Farb und Geruchstoffe</li><li>OHNE Paraffine</li><li>OHNE Silikone</li><li>Mit reinem Hanfsamenöl</li></ul>
  <p class="badge" style="top:238px">PRODUKT NICHT<br>AN TIEREN GETESTET</p>
  <p class="copy">Hautmilde waschaktive Bestandteile entfalten eine besonders angenehme und schonende Reinigungswirkung. Hochwertiges Hanfsamen-Öl pflegt das Haar auf natürliche Weise und macht es angenehm weich, locker und geschmeidig.<br><br><strong>HANF - SHAMPOO</strong> - eignet sich für alle Haartypen, besonders für strapaziertes und mattes Haar.</p>
  <p class="inci" style="top:143px">Ingredients (INCI): Aqua, Sodium Laureth Sulfate, TEA-Lauryl Sulfate, Disodium Laureth Sulfosuccinate, Potassium Cocoyl Hydrolized Collagen, Linoleamide-DEA, Cannabis Sativa Seed Oil, Natural Perfume, Sodium Chloride, Citric Acid, Potassium Sorbate, Panthenol, Tocopherol, Chlorophyll, Citral*, Citronellol*, Geraniol*, Limonene*, Linalool*.<br>(* natürliche Bestandteile ätherischer Öle).</p>
  <div class="facts"><div class="qty">200<small>ml</small></div><div class="estim">e</div><div><svg width="22" height="20" viewBox="0 0 22 20" fill="none" stroke="#fff" stroke-width="1"><path d="M3 8h16l-1.5 10h-13z"/><path d="M4 8l12-6"/><text x="7" y="16" font-size="5" fill="#fff" stroke="none" font-family="sans-serif">12m</text></svg></div></div>
  <p class="maker">HERSTELLER: MORVIL NATURKOSMETIK A- 4812 GRUNDLACH</p>
</section>

<!-- Körperlotion -->
<section class="label big tone-brown" style="left:23px;top:310px">
  <div class="texture" role="img" aria-label="Fließende braune Textur als Hintergrund"></div>
  <div class="brand"><span class="dot"></span><span class="brand-name">BRISK MEADOW</span></div>
  <h2 class="product-name" style="font-size:23px">HANF-KÖRPERLOTION</h2>
  <p class="slogan">FEEL THE NATURE</p>
  <ul class="claims"><li>OHNE künstliche Farb und Geruchstoffe</li><li>OHNE Paraffine</li><li>OHNE Silikone</li><li>Mit reinem Hanfsamenöl</li></ul>
  <p class="badge">PRODUKT NICHT<br>AN TIEREN GETESTET</p>
  <p class="copy">Reines Hanfsamen-Öl pflegt die Haut auf natürliche Weise, verhindert zu starkes Austrocknen und macht sie besonders weich und geschmeidig.<br><br><strong>HANF-KÖRPERLOTION</strong> - ist zur angenehmen Körperpflege, besonders nach dem Baden, vor allem bei trockener, spröder und empfindlicher Haut.</p>
  <p class="inci" style="top:152px">Ingredients (INCI): Aqua, Cannabis Sativa Seed Oil, Cetearyl Alcohol, Ceteareth-12, Cetearyl Glucoside, Glycerine, Hexyldecanol, Natural Perfume, Benzyl Alcohol, Potassium Sorbate, Sodium Benzoate, Tocopherol, Panthenol, Citric Acid, Geraniol*, Limonene*, Linalool*, Citronellol*, Citral*.<br>(* natürliche Bestandteile ätherischer Öle).</p>
  <div class="facts"><div class="qty">200<small>ml</small></div><div class="estim">e</div><div><svg width="22" height="20" viewBox="0 0 22 20" fill="none" stroke="#fff" stroke-width="1"><path d="M3 8h16l-1.5 10h-13z"/><path d="M4 8l12-6"/><text x="7" y="16" font-size="5" fill="#fff" stroke="none" font-family="sans-serif">12m</text></svg></div></div>
  <p class="maker">HERSTELLER: MORVIL NATURKOSMETIK A- 4812 GRUNDLACH</p>
</section>

<!-- Haarbalsam -->
<section class="label big tone-gold" style="left:436px;top:310px">
  <div class="texture" role="img" aria-label="Fließende goldgelbe Textur als Hintergrund"></div>
  <div class="brand"><span class="dot"></span><span class="brand-name">BRISK MEADOW</span></div>
  <h2 class="product-name" style="font-size:23px">HANF-HAARBALSAM</h2>
  <p class="slogan">FEEL THE NATURE</p>
  <ul class="claims"><li>OHNE künstliche Farb und Geruchstoffe</li><li>OHNE Paraffine</li><li>OHNE Silikone</li><li>Mit reinem Hanfsamenöl</li></ul>
  <p class="badge">PRODUKT NICHT<br>AN TIEREN GETESTET</p>
  <p class="copy" style="top:16px">Eine spezielle Kombination von naturreinem Hanfsamen-Öl und weiteren hochwertigen Pflanzenölen pflegt das Haar hervorragend und macht es angenehm weich, locker, geschmeidig, natürlich glänzend, äusserst leicht frisierbar und verhindert wirksam die Spaltung der Spitzen.<br><strong>HANF-HAARBALSAM</strong> - eignet sich für alle Haartypen, besonders für strapaziertes, geschädigtes, brüchiges und mattes Haar, sowie bei gespaltenen Haarspitzen.</p>
  <p class="inci" style="top:151px">Ingredients (INCI): Aqua, Ceteareth-20, Cetearyl Alcohol, Dicocodimonium Chloride, Glycerine, Cannabis Sativa Seed Oil, Coco-Glucoside, Glyceryl Oleate, Natural Perfume, Potassium Sorbate, Panthenol, Citric Acid, Tocopherol, Chlorophyll, Citral*, Citronellol*, Geraniol*, Limonene*, Linalool*.<br>(* natürliche Bestandteile ätherischer Öle).</p>
  <div class="facts"><div class="qty">200<small>ml</small></div><div class="estim">e</div><div><svg width="22" height="20" viewBox="0 0 22 20" fill="none" stroke="#fff" stroke-width="1"><path d="M3 8h16l-1.5 10h-13z"/><path d="M4 8l12-6"/><text x="7" y="16" font-size="5" fill="#fff" stroke="none" font-family="sans-serif">12m</text></svg></div></div>
  <p class="maker">HERSTELLER: MORVIL NATURKOSMETIK A- 4812 GRUNDLACH</p>
</section>

<!-- Schaumbad -->
<section class="label big tone-wine" style="left:23px;top:598px">
  <div class="texture" role="img" aria-label="Fließende weinrote Textur als Hintergrund"></div>
  <div class="brand"><span class="dot"></span><span class="brand-name">BRISK MEADOW</span></div>
  <h2 class="product-name">HANF-SCHAUMBAD</h2>
  <p class="slogan">FEEL THE NATURE</p>
  <ul class="claims"><li>OHNE künstliche Farb und Geruchstoffe</li><li>OHNE Paraffine</li><li>OHNE Silikone</li><li>Mit reinem Hanfsamenöl</li></ul>
  <p class="badge">PRODUKT NICHT<br>AN TIEREN GETESTET</p>
  <p class="copy">Hautmilde waschaktive Bestandteile entwickeln einen besonders milden und cremigen Schaum. Die hervorragende Pflegewirkung von naturreinem Hanfsamen-Öl macht die Haut außergewöhnlich weich und geschmeidig.<br><br><strong>HANF-SCHAUMBAD</strong> - eignet sich zur milden Reinigung und Pflege, besonders von empfindlicher, rauer und rissiger Haut.</p>
  <p class="inci" style="top:145px">Ingredients (INCI): Aqua, MIPA-Pareth-25-Sulfate, Cocamidopropyl Betaine, Disodium Laureth Sulfosuccinate, Linoleamide-DEA, Cannabis Sativa Seed Oil, Coco-Glucoside, Glyceryl Oleate, Natural Perfume, Panthenol, Potassium Sorbate, Citric Acid, Tocopherol, Chlorophyll, Citral*, Citronellol*, Geraniol*, Limonene*, Linalool*.<br>(* natürliche Bestandteile ätherischer Öle).</p>
  <div class="facts"><div class="qty">200<small>ml</small></div><div class="estim">e</div><div><svg width="22" height="20" viewBox="0 0 22 20" fill="none" stroke="#fff" stroke-width="1"><path d="M3 8h16l-1.5 10h-13z"/><path d="M4 8l12-6"/><text x="7" y="16" font-size="5" fill="#fff" stroke="none" font-family="sans-serif">12m</text></svg></div></div>
  <p class="maker">HERSTELLER: MORVIL NATURKOSMETIK A- 4812 GRUNDLACH</p>
</section>

<!-- Lippenbalsam -->
<section class="label tone-lip" style="left:436px;top:623px;width:389px;height:247px">
  <div class="texture" role="img" aria-label="Fließende hellblaue Textur als Hintergrund"></div>
  <div class="brand" style="left:0;width:175px;top:12px"><span class="dot"></span><span class="brand-name">BRISK MEADOW</span></div>
  <h2 class="product-name" style="left:0;width:175px;top:60px;font-size:23px">LIPPENBALSAM</h2>
  <p class="slogan" style="left:10px;width:150px;top:98px;font-size:7.5px;letter-spacing:4px">FEEL THE NATURE</p>
  <ul class="claims" style="left:12px;top:124px"><li>OHNE künstliche Farb<br>und Geruchstoffe</li><li>OHNE Paraffine</li><li>OHNE Silikone</li><li>Mit reinem Hanfsamenöl</li></ul>
  <p class="badge" style="left:10px;top:205px">PRODUKT NICHT<br>AN TIEREN GETESTET</p>
  <p class="copy" style="left:200px;width:150px;top:10px;font-size:7px">Natürliches Hanfsamenöl, reines Bienenwachs und weitere wertvolle Bestandteile pflegen die Lippen nachhaltig und schützen sie vor ungünstigen Witterungseinflüssen und Austrocknung.<br><br><strong>LIPPENBALSAM</strong> - eignet sich besonders zur nachhaltigen Pflege von empfindlichen, spröden und zu Rissen neigenden Lippen.</p>
  <p class="inci" style="left:200px;width:150px;top:142px;font-size:5.3px">Ingredients (INCI): Cannabis sativa Seed Oil, Cocos nucifera Oil, Cera Alba, Natural Perfume, Citral*, Citronellol*, Geraniol*, Limonene*, Linalool*.<br>(* natürliche Bestandteile ätherischer Öle).</p>
  <p class="maker" style="left:200px;top:205px;font-size:5.5px;font-weight:400;line-height:1.35">HERSTELLER:<br>MORVIL NATURKOSMETIK<br>A-4812 GRUNDLACH</p>
  <div style="left:310px;top:196px;border-left:1px solid #fff;padding-left:6px;text-align:center;line-height:1"><div style="font-size:16px">6<small style="font-size:9px">g</small></div><div style="font-size:15px;border-top:1px solid #fff;margin-top:2px">e</div></div>
</section>

<!-- Handcreme front -->
<section class="label tone-grey" style="left:23px;top:907px;width:389px;height:118px">
  <div class="texture" role="img" aria-label="Fließende graue Textur als Hintergrund"></div>
  <div class="brand" style="left:0;width:217px;top:14px"><span class="dot" style="width:24px;height:24px"></span><span class="brand-name" style="font-size:8.5px">BRISK MEADOW</span></div>
  <h2 class="product-name" style="left:0;width:217px;top:56px;font-size:22px">HANF-HANDCREME</h2>
  <p class="slogan" style="left:20px;width:177px;top:90px;border:none;font-size:7.5px">FEEL THE NATURE</p>
  <ul class="claims" style="left:217px;top:8px;font-size:7.5px"><li>OHNE künstliche Farb und Geruchstoffe</li><li>OHNE Paraffine</li><li>OHNE Silikone</li><li>Mit reinem Hanfsamenöl</li></ul>
  <div style="left:337px;top:52px;border-left:1px solid #fff;padding-left:5px;font-size:15px">50<small style="font-size:9px">g</small></div>
  <p class="badge" style="left:214px;top:84px;width:160px;text-align:center">PRODUKT NICHT AN TIEREN GETESTET</p>
</section>

<!-- Handcreme back -->
<section class="label tone-grey" style="left:23px;top:1039px;width:389px;height:118px">
  <div class="texture" role="img" aria-label="Fließende graue Textur als Hintergrund"></div>
  <p class="copy" style="left:9px;width:205px;top:9px;font-size:8px">Der hohe Gehalt an reinem Hanfsamenöl und natürlichem Bienenwachs schützt und pflegt die Haut hervorragend und macht sie weich und geschmeidig.<br>HANF-HANDCREME - eignet sich zur schützenden Pflege besonders von strapazierter, empfindlicher und spröder Haut.</p>
  <p class="inci" style="left:229px;width:152px;top:15px;font-size:5.3px">Cannabis sativa Seed Oil, Cocos Nucifera Oil, Cera Alba, Tocopherol, Natural Perfume, Citral*, Citronellol*, Geraniol*, Limonene*, Linalool*.<br>(* natürliche Bestandteile ätherischer Öle).</p>
  <p class="maker" style="left:229px;top:85px;width:130px;border-top:1px solid #fff;padding-top:4px;font-size:5.8px;font-weight:400;line-height:1.6">HERSTELLER: MORVIL NATURKOSMETIK<br>A-4812 GRUNDLACH</p>
  <div style="left:362px;top:85px;border-left:1px solid #fff;padding-left:5px;font-size:15px;height:28px">e</div>
</section>

<!-- Gesichtscreme front -->
<section class="label tone-violet" style="left:436px;top:907px;width:389px;height:118px">
  <div class="texture" role="img" aria-label="Fließende violette Textur als Hintergrund"></div>
  <div class="brand" style="left:0;width:217px;top:14px"><span class="dot" style="width:24px;height:24px"></span><span class="brand-name" style="font-size:8.5px">BRISK MEADOW</span></div>
  <h2 class="product-name" style="left:0;width:217px;top:56px;font-size:21px">HANF-GESICHTSCREME</h2>
  <p class="slogan" style="left:20px;width:177px;top:90px;border:none;font-size:7.5px">FEEL THE NATURE</p>
  <ul class="claims" style="left:217px;top:8px;font-size:7.5px"><li>OHNE künstliche Farb und Geruchstoffe</li><li>OHNE Paraffine</li><li>OHNE Silikone</li><li>Mit reinem Hanfsamenöl</li></ul>
  <div style="left:337px;top:52px;border-left:1px solid #fff;padding-left:5px;font-size:15px">50<small style="font-size:9px">g</small></div>
  <p class="badge" style="left:214px;top:84px;width:160px;text-align:center;background:rgba(20,0,60,.55)">PRODUKT NICHT AN TIEREN GETESTET</p>
</section>

<!-- Gesichtscreme back -->
<section class="label tone-violet" style="left:436px;top:1039px;width:389px;height:118px">
  <div class="texture" role="img" aria-label="Fließende violette Textur als Hintergrund"></div>
  <p class="copy" style="left:12px;width:205px;top:9px;font-size:8px">Der besonders hohe Gehalt an reinem Hanfsamen-Öl pflegt die Haut hervorragend und macht sie ungewöhnlich weich und geschmeidig.<br>HANF-GESICHTSCREME - eignet sich zur angenehmen und feuchtigkeitsspendenden Pflege der gesamten Gesichtspartie besonders bei trockener und spröder Haut.</p>
  <p class="inci" style="left:229px;width:154px;top:8px;font-size:5.1px">Ingredients (INCI): Aqua, Cannabis Sativa Seed Oil, Cetearyl Alcohol, Cetearyl Glucoside, Sodium Cetearyl Sulfate, Hexyldecanol, Glycerine, Natural Perfume, Benzyl Alcohol, Potassium Sorbate, Sodium Benzoate, Tocopherol, Panthenol, Citric Acid, Citral*, Citronellol*, Geraniol*, Limonene*, Linalool*.<br>(* natürliche Bestandteile ätherischer Öle).</p>
  <p class="maker" style="left:229px;top:85px;width:130px;border-top:1px solid #fff;padding-top:4px;font-size:5.8px;font-weight:400;line-height:1.6">HERSTELLER: MORVIL NATURKOSMETIK<br>A-4812 GRUNDLACH</p>
  <div style="left:362px;top:85px;border-left:1px solid #fff;padding-left:5px;font-size:15px;height:28px">e</div>
</section>

</body>
</html>
```